Top Pour Web site design

The aim of Top Pour is to provide an online service which allows customers to pre-order drinks and gain incentives such as fast entry, special offers (drinks, entry fees), as well as allowing customers to compare drinking establishments based upon costs and ratings.

what is required is the design of the pages stated below completed to the specifications.

Target Market(s)

The target market of Top Pour is men and women between the ages of 18 to 26 mainly. Within the age range of 18 to 26 the more specific target groups

Industry/Entity Type

Online

Requirements
Must have
• What is required to be designed

Website to be viewable on different systems e.g desktop, laptop and for mobile devices a mobile friendly page

Home page

Logo
Company name
Log in
Sign up
Help
Social media links, Follow us link

Bar, pub, club search function
Search by postcode, establishment type, distance

Pictorial instructions of how to use the site like ( quick dine). The stages are 1) select location 2) build order and pay 3) pick up from bar

Pre load results of establishments

Drinking establishment sign up

Map showing search results

List of results

My basket window which shows your order

Pop out box for customer sign up

Buttons for FAQ, general information, company information, Privacy policy ect at bottom of page

The home page is required to be Clear, simple, easy to use and stylish but not over the top with to much information which will confuse the customers. The preloaded results need to be obvious and where can be seen. The pictorial instructions should go below the preloaded results. Once the search criteria has been filled in and has been submitted the preloaded results and pictorial instructions will be removed and be replaced by the map and search results.

Drinking establishment personal page requires

Details of drinking establishment (name, address, contact, map)
list of drinks avliable
My basket
Special Offers
Gallery
Calendar
Reviews section at the bottom

When a person clicks on a drinking establishment page what that person should see when they open the page is company name logo
with a list of the drinks they offer and special offers. Tabs or buttons for gallery, establishment details, calender and special offers should be located along top or down the left. when they are clicked on they will replace the menu.

The colour scheme is based around the logo which is attached. We do not want any pink or overly bright colours which would not go with the logo.

A site which we like is this one
http://www.quick-dine.example.co.uk/
this site is perfect simple, clear but also good looking. If you need inspiration you should use this site as a starting point.
Should not have
• what should be avoided is a site which like this one http://platepoint.example.co.uk/~beta/?gclid=XQMWpLaRtnfGDsHYbTqeKZPLv

it is to complicated with bad font and colours. The site just feels cheesy and not classy. we like very little about this site

```html
<!DOCTYPE html>
<html lang="en">
<head>
<meta charset="utf-8">
<title>Top Pour – Drinking Establishment</title>
<link href="https://fonts.googleapis.com/css2?family=Open+Sans:wght@400;600;700&family=Short+Stack&display=swap" rel="stylesheet">
<style>
:root{
  --brand:#2e3192;
  --brand-dark:#262a80;
  --btn-top:#6367e0;
  --btn-bottom:#3c40bd;
  --text:#333;
  --muted:#555;
  --light-grey:#e6e6e6;
  --line:#c9c9c9;
  --gold:#d9a21b;
  --footer-muted:#9fa2d8;
}
*{box-sizing:border-box;margin:0;padding:0}
html,body{width:1187px;height:1200px;overflow:hidden;background:#fff}
body{font-family:'Open Sans',sans-serif;color:var(--text);position:relative}
.abs{position:absolute}
.top-band{left:0;top:0;width:1187px;height:6px;background:#bdbdbd}

/* header */
.logo{left:182px;top:30px;display:flex;align-items:center;gap:12px}
.logo-mark{width:72px;height:72px;border-radius:50%;background:#8a8a8a}
.logo-name{font-size:30px;font-weight:600;color:var(--brand)}
.social{display:flex;gap:3px}
.social span{width:24px;height:24px;border-radius:50%;background:var(--brand);display:block}
.social.header{left:903px;top:24px}
.cart{left:551px;top:61px;font-size:12.5px;color:#666;display:flex;align-items:center;gap:6px}
.cart .num{color:#3b4ad0;font-weight:600}
.cart .sub{color:#3b4ad0;font-weight:700}
.btn-grey{border:1px solid #aaa;background:linear-gradient(#f2f2f2,#d4d4d4);color:#444;font-size:12.5px;padding:2px 9px;margin-left:4px}
.account{left:817px;top:60px;font-size:14.5px;font-weight:600;color:#444}
.help{left:928px;top:59px;width:79px;height:22px;border:1px solid #bbb;border-radius:4px;font-size:12px;color:#3b4ad0;display:flex;align-items:center;justify-content:center;box-shadow:0 1px 2px rgba(0,0,0,.2)}
.rule{left:181px;top:123px;width:820px;height:1px;background:#ddd}
.page-title{left:182px;top:132px;font-family:'Short Stack',cursive;font-size:23px;color:var(--brand)}

/* sidebar */
.map{left:181px;top:184px;width:196px;height:160px;border:1px solid #ccc;padding:5px;background:#fff}
.map div{width:100%;height:100%;background:linear-gradient(135deg,#e9e5da,#f3f0e6 50%,#dcd6c5)}
.side-btn{left:181px;width:196px;height:31px;border:1px solid #bbb;background:linear-gradient(#f1f1f1,#cfcfcf);display:flex;align-items:center;gap:10px;padding-left:10px;font-size:13.5px;color:#555;text-transform:uppercase}
.side-btn svg{width:15px;height:15px;fill:#999}
.creator{left:181px;top:563px;width:196px;height:249px;background:var(--brand);padding:14px 17px}
.creator h3{font-family:'Short Stack',cursive;font-weight:400;font-size:20px;color:#fff;margin:0 0 8px 1px}
.select{position:relative;height:31px;background:#fff;border:1px solid #aaa;font-size:14px;color:#555;padding:4px 9px;margin-bottom:7px}
.select::after{content:"";position:absolute;right:9px;top:13px;border:4px solid transparent;border-top:5px solid #222}
.search-btn{margin-top:10px;width:156px;height:31px;background:linear-gradient(var(--btn-top),var(--btn-bottom));color:#fff;font-weight:700;font-size:16px;display:flex;align-items:center;justify-content:center;gap:8px;box-shadow:0 2px 2px rgba(0,0,0,.3)}

/* establishment */
.venue-photo{left:396px;top:184px;width:109px;height:109px;background:linear-gradient(#4a4a4a,#1f1f1f 60%,#6a6a6a);box-shadow:1px 1px 3px rgba(0,0,0,.4)}
.venue-name{left:521px;top:179px;font-size:17px;font-weight:700;color:var(--brand)}
.facts{left:521px;top:204px;font-size:12px;line-height:20.5px}
.facts dt{position:absolute;left:0;font-weight:700;color:#444}
.facts dd{margin-left:91px;color:#555}
.cost{color:var(--gold);font-weight:700;letter-spacing:2px}
.when{left:856px;top:205px;font-size:12px;font-weight:600;color:#444}
.day{left:856px;top:227px;width:135px;height:32px;border:1px solid #ccc;box-shadow:0 1px 2px rgba(0,0,0,.15);font-size:12.5px;color:#555;padding:7px 7px}
.day::after{content:"";position:absolute;right:9px;top:13px;border:4px solid transparent;border-top:5px solid #222}
.dash{height:0;border-top:1px dashed #bbb}
.also{left:397px;top:328px;font-family:'Short Stack',cursive;font-size:18px;color:#444}
.cat{left:397px;font-size:16px;font-weight:600;color:var(--brand)}

.item{width:292px;height:72px}
.item .thumb{position:absolute;left:0;top:0;width:71px;height:72px;border:1px solid #bbb}
.item h4{position:absolute;left:77px;top:-3px;font-size:13.8px;font-weight:600;color:#333;white-space:nowrap}
.item p{position:absolute;left:77px;top:18px;font-size:12px;color:#444;white-space:nowrap}
.item .qty{position:absolute;left:76px;top:42px;width:74px;height:30px;border:1px solid #ccc;font-size:12.5px;color:#555;display:flex;align-items:center;justify-content:center}
.item .add{position:absolute;left:157px;top:42px;width:117px;height:30px;background:linear-gradient(var(--btn-top),var(--btn-bottom));border:1px solid #3236a8;color:#fff;font-weight:700;font-size:13.5px;display:flex;align-items:center;justify-content:center;box-shadow:0 2px 2px rgba(0,0,0,.3)}

/* footer */
.footer{left:0;top:1094px;width:1187px;height:106px;background:var(--brand)}
.foot-links{left:179px;top:1130px;font-size:12.3px;color:#fff}
.copyright{left:179px;top:1150px;font-size:12.3px;color:var(--footer-muted)}
.social.footer span{background:#fff;width:22px;height:22px}
.social.footer{left:895px;top:1135px;gap:4px}
</style>
</head>
<body>
<div class="abs top-band"></div>

<div class="abs logo"><span class="logo-mark"></span><span class="logo-name">Top Pour</span></div>
<div class="abs social header" aria-label="Follow us"><span></span><span></span><span></span><span></span></div>
<div class="abs cart">
  <svg width="14" height="12" viewBox="0 0 14 12"><path d="M0 1h2.5l2 7h7l1.5-5H4" fill="none" stroke="#555" stroke-width="1.6"/><circle cx="5.5" cy="10.5" r="1.3" fill="#555"/><circle cx="10.5" cy="10.5" r="1.3" fill="#555"/></svg>
  <span><span class="num">0</span> items | Subtotal : <span class="sub">£0.0</span></span>
  <span class="btn-grey">Checkout</span>
</div>
<div class="abs account">Log in . Sign up</div>
<div class="abs help">NEED HELP</div>
<div class="abs rule"></div>
<h1 class="abs page-title">Drinking Establishment</h1>

<!-- sidebar -->
<div class="abs map"><div role="img" aria-label="Street map showing the establishment location"></div></div>
<div class="abs side-btn" style="top:355px"><svg viewBox="0 0 16 16"><path d="M1 9l8-8h6v6l-8 8z"/></svg>Entry Tickets</div>
<div class="abs side-btn" style="top:394px"><svg viewBox="0 0 16 16"><circle cx="8" cy="8" r="7"/></svg>Special Offers</div>
<div class="abs side-btn" style="top:433px"><svg viewBox="0 0 16 16"><path d="M1 3h14v12H1zM3 6h10v7H3z" fill-rule="evenodd"/></svg>Calender</div>
<div class="abs side-btn" style="top:472px"><svg viewBox="0 0 16 16"><path d="M1 2h14v12H1zM2.5 3.5v9h11v-9z M3 12l4-5 3 3 2-2 2 4z" fill-rule="evenodd"/></svg>Gallery</div>
<div class="abs side-btn" style="top:511px"><svg viewBox="0 0 16 16"><path d="M1 3h14v10H1z M1 3l7 6 7-6" /></svg>Contact Details</div>

<div class="abs creator">
  <h3>Drink Creator</h3>
  <div class="select">Drink Type</div>
  <div class="select">Ingredient 1</div>
  <div class="select">Ingredient 2</div>
  <div class="select">Ingredient 3</div>
  <div class="search-btn">SEARCH NOW
    <svg width="16" height="16" viewBox="0 0 16 16"><circle cx="6.5" cy="6.5" r="4.5" fill="none" stroke="#fff" stroke-width="2"/><path d="M10 10l5 5" stroke="#fff" stroke-width="2.4"/></svg>
  </div>
</div>

<!-- establishment details -->
<div class="abs venue-photo" role="img" aria-label="Photo of the pub frontage"></div>
<h2 class="abs venue-name">The LANTERN</h2>
<dl class="abs facts">
  <dt>Provides</dt><dd>: Food &amp; Drink</dd>
  <dt>Special offers</dt><dd>: 15% Off</dd>
  <dt>Cost</dt><dd>: <span class="cost">£££££</span></dd>
  <dt>Rating</dt><dd>: <svg width="88" height="13" viewBox="0 0 88 13" style="vertical-align:-2px">
    <g fill="#4c50c8"><rect x="2" y="1" width="10" height="12" rx="1"/><rect x="20" y="1" width="10" height="12" rx="1"/><rect x="38" y="1" width="10" height="12" rx="1"/><rect x="56" y="1" width="10" height="12" rx="1"/></g>
    <rect x="74" y="1" width="10" height="12" rx="1" fill="#c8c8c8"/></svg></dd>
</dl>
<div class="abs when">When do you want to go</div>
<div class="abs day">Select Order Day</div>
<div class="abs dash" style="left:396px;top:312px;width:599px"></div>
<h2 class="abs also">Establishment also offers</h2>

<!-- Wines -->
<h3 class="abs cat" style="top:363px">Wines</h3>
<div class="abs item" style="left:397px;top:394px"><div class="thumb" role="img" aria-label="Red wine splashing in a glass" style="background:linear-gradient(135deg,#f5e9ea,#9b1c2e)"></div><h4>Duis sed lectus sit amet</h4><p>Nulla cursus ligula nec neque porttitor</p><div class="qty">How Many</div><div class="add">ADD TO ORDER</div></div>
<div class="abs item" style="left:703px;top:394px"><div class="thumb" role="img" aria-label="Glass of red wine outdoors" style="background:linear-gradient(#8fa86a,#b3132a 60%,#5d6b3c)"></div><h4>Donec non urna et ligula</h4><p>Etiam tempor sapien ac arcu</p><div class="qty">How Many</div><div class="add">ADD TO ORDER</div></div>
<div class="abs dash" style="left:396px;top:485px;width:293px"></div>
<div class="abs dash" style="left:701px;top:485px;width:294px"></div>
<div class="abs item" style="left:397px;top:503px"><div class="thumb" role="img" aria-label="Wine glass with red wine" style="background:radial-gradient(circle at 50% 55%,#7a1620,#d6a25a 75%,#f2d9a8)"></div><h4>Nullam nisi risus</h4><p>Nullam enim magna, laoreet ut</p><div class="qty">How Many</div><div class="add">ADD TO ORDER</div></div>
<div class="abs item" style="left:703px;top:503px"><div class="thumb" role="img" aria-label="Red wine poured from a bottle" style="background:linear-gradient(90deg,#f7f7f7,#e8d6d6 50%,#a21a2c)"></div><h4>Maecenas non lorem</h4><p>Praesent et nulla nisl</p><div class="qty">How Many</div><div class="add">ADD TO ORDER</div></div>
<div class="abs dash" style="left:396px;top:593px;width:293px"></div>
<div class="abs dash" style="left:701px;top:593px;width:294px"></div>

<!-- Beers -->
<h3 class="abs cat" style="top:618px">Beers</h3>
<div class="abs item" style="left:397px;top:650px"><div class="thumb" role="img" aria-label="Beer splashing in a glass" style="background:radial-gradient(circle,#f4dca0,#b56b12 60%,#3a2208)"></div><h4>Duis sed lectus sit amet</h4><p>Nulla cursus ligula nec neque porttitor</p><div class="qty">How Many</div><div class="add">ADD TO ORDER</div></div>
<div class="abs item" style="left:703px;top:650px"><div class="thumb" role="img" aria-label="Several glasses of beer" style="background:linear-gradient(#f3efe6,#d9962a 50%,#8b5a1c)"></div><h4>Donec non urna et ligula</h4><p>Etiam tempor sapien ac arcu</p><div class="qty">How Many</div><div class="add">ADD TO ORDER</div></div>
<div class="abs dash" style="left:396px;top:739px;width:293px"></div>
<div class="abs dash" style="left:701px;top:739px;width:294px"></div>

<!-- Cocktails -->
<h3 class="abs cat" style="top:763px">Cocktails</h3>
<div class="abs item" style="left:397px;top:795px"><div class="thumb" role="img" aria-label="Red cocktails being prepared" style="background:linear-gradient(#c41c12,#f0541e 60%,#a4150d)"></div><h4>Duis sed lectus sit amet</h4><p>Nulla cursus ligula nec neque porttitor</p><div class="qty">How Many</div><div class="add">ADD TO ORDER</div></div>
<div class="abs item" style="left:703px;top:795px"><div class="thumb" role="img" aria-label="Row of cocktail glasses" style="background:linear-gradient(#d9dfe4,#e85a3a 50%,#4b5e3a)"></div><h4>Donec non urna et ligula</h4><p>Etiam tempor sapien ac arcu</p><div class="qty">How Many</div><div class="add">ADD TO ORDER</div></div>
<div class="abs dash" style="left:396px;top:884px;width:293px"></div>
<div class="abs dash" style="left:701px;top:884px;width:294px"></div>

<!-- Non alcoholic -->
<h3 class="abs cat" style="top:908px">Non alcoholic</h3>
<div class="abs item" style="left:397px;top:940px"><div class="thumb" role="img" aria-label="Orange fruit drink with straw" style="background:radial-gradient(circle at 50% 45%,#f2561a,#fbb27a 45%,#fff 70%)"></div><h4>Duis sed lectus sit amet</h4><p>Nulla cursus ligula nec neque porttitor</p><div class="qty">How Many</div><div class="add">ADD TO ORDER</div></div>
<div class="abs item" style="left:703px;top:940px"><div class="thumb" role="img" aria-label="Strawberry smoothie with strawberries" style="background:linear-gradient(#c9e3a4,#f3c7c4 50%,#c5161f)"></div><h4>Donec non urna et ligula</h4><p>Etiam tempor sapien ac arcu</p><div class="qty">How Many</div><div class="add">ADD TO ORDER</div></div>
<div class="abs dash" style="left:396px;top:1030px;width:293px"></div>
<div class="abs dash" style="left:701px;top:1030px;width:294px"></div>

<!-- footer -->
<footer class="abs footer"></footer>
<div class="abs foot-links">FAQ &nbsp;|&nbsp; general information &nbsp;|&nbsp; company information &nbsp;|&nbsp; Privacy policy</div>
<div class="abs copyright">Copyright © 2013 Top Pour. All rights reserved</div>
<div class="abs social footer" aria-label="Follow us"><span></span><span></span><span></span><span></span></div>
</body>
</html>
```